Business card design for new eCommerce site focusing on integrity and strong businsess tactics

We need a business card that will stand out and be memorable. Something with color that matches our company logo colors. Think high end version of Pactivo. There are 2 logos provided. The parent company is called Amber Ledge Partners and we are presenting a new and very exciting eCommerce site called BrightHarborTrade.example.

Target Market(s)

Our target markets are in the Activities, Food and Beverage, Health and Beauty

Industry/Entity Type

Marketing

Contact Information for Business Card

We have 4 members that need cards...I will provide all info to the winner of the design contest
Business Address is
4870 West 63rd Avenue, Suite C207
Phoenix AZ 85731

Font styles to use
Serif
Sans Serif

Colors

Designer to choose colors to be used in the design.

Requirements
Must have
• The card must be memorable...should be unique in design but must exude integrity and be playful .
• I have provided several colors or our parent company...please feel free to use which ever
Nice to have
• I will leave this up to you. Feel free to use other images of your choosing that wraps around our client.....Activities, Dining, Health, Beauty
Should not have
• just dont be boring

```html
<!DOCTYPE html>
<html lang="en">
<head>
<meta charset="utf-8">
<title>BrightHarborTrade.example business cards</title>
<link href="https://fonts.googleapis.com/css2?family=Questrial&display=swap" rel="stylesheet">
<style>
  :root {
    --stage: #2b2b2d;
    --paper: #f7f7f7;
    --paper-shade: #e9e9ea;
    --brand-blue: #2a86b8;
    --brand-blue-deep: #1f6fa3;
    --brand-green: #72b33a;
    --ink-grey: #6a6a6a;
    --white: #ffffff;
  }
  * { margin: 0; padding: 0; box-sizing: border-box; }
  html, body { width: 1200px; height: 834px; overflow: hidden; }
  body {
    background: var(--stage);
    font-family: "Questrial", "Century Gothic", sans-serif;
    position: relative;
  }
  .card {
    position: absolute;
    width: 620px;
    height: 354px;
    background: linear-gradient(135deg, var(--white) 0%, var(--paper) 55%, var(--paper-shade) 100%);
    overflow: hidden;
    box-shadow: 0 10px 30px rgba(0,0,0,0.45);
  }
  .card--front { left: 70px; top: 60px; }
  .card--back { left: 510px; top: 420px; }
  .card svg.shape { position: absolute; inset: 0; width: 100%; height: 100%; }

  .brand { position: absolute; display: flex; align-items: center; gap: 10px; z-index: 1; }
  .brand__dot { width: 30px; height: 30px; border-radius: 50%; background: var(--brand-blue); flex: none; }
  .brand__name { color: var(--brand-green); font-size: 26px; line-height: 1; letter-spacing: -0.3px; white-space: nowrap; }
  .brand__tagline { color: var(--ink-grey); font-size: 13px; letter-spacing: 0.6px; margin-top: 5px; white-space: nowrap; }
  .card--front .brand { left: 56px; top: 130px; }

  .partner { position: absolute; right: 48px; top: 44px; display: flex; flex-direction: column; align-items: center; gap: 6px; z-index: 1; }
  .partner__badge { width: 54px; height: 54px; border-radius: 50%; background: var(--brand-green); }
  .partner__name { color: var(--brand-green); font-size: 13px; white-space: nowrap; }

  .card--back .brand { left: 370px; top: 150px; gap: 8px; }
  .card--back .brand__dot { width: 22px; height: 22px; }
  .card--back .brand__name { font-size: 17px; }
  .card--back .brand__tagline { font-size: 9.5px; margin-top: 4px; letter-spacing: 0.4px; }

  .contact { position: absolute; left: 40px; top: 78px; color: var(--white); z-index: 1; }
  .contact__name { font-size: 19px; letter-spacing: 1px; font-weight: 700; }
  .contact__role { color: var(--brand-green); font-size: 14px; margin-top: 2px; }
  .contact__address { font-size: 12px; line-height: 1.55; margin-top: 14px; }
  .contact__lines { list-style: none; margin-top: 14px; font-size: 12px; }
  .contact__lines li { display: flex; align-items: center; gap: 9px; height: 20px; }
  .contact__lines svg { width: 12px; height: 12px; flex: none; }
</style>
</head>
<body>

  <section class="card card--front">
    <svg class="shape" viewBox="0 0 620 354" preserveAspectRatio="none" aria-hidden="true">
      <path d="M0,282 C150,294 250,324 360,294 C460,264 520,220 620,220 L620,354 L0,354 Z" fill="var(--brand-green)"/>
      <path d="M0,289 C150,301 250,331 360,301 C460,271 520,227 620,227 L620,354 L0,354 Z" fill="var(--white)"/>
      <path d="M0,293 C150,305 250,335 360,305 C460,275 520,231 620,231 L620,354 L0,354 Z" fill="var(--brand-blue)"/>
    </svg>
    <div class="brand">
      <span class="brand__dot"></span>
      <div>
        <div class="brand__name">BrightHarborTrade.example</div>
        <div class="brand__tagline">Activities-Dining-Health-Beauty</div>
      </div>
    </div>
    <div class="partner">
      <span class="partner__badge"></span>
      <span class="partner__name">Amber Ledge Partners</span>
    </div>
  </section>

  <section class="card card--back">
    <svg class="shape" viewBox="0 0 620 354" aria-hidden="true">
      <defs>
        <linearGradient id="blueFill" x1="0" y1="0" x2="0" y2="1">
          <stop offset="0" stop-color="var(--brand-blue)"/>
          <stop offset="1" stop-color="var(--brand-blue-deep)"/>
        </linearGradient>
      </defs>
      <circle cx="40" cy="270" r="322" fill="none" stroke="var(--brand-green)" stroke-width="12"/>
      <circle cx="40" cy="270" r="304" fill="var(--white)"/>
      <circle cx="40" cy="270" r="298" fill="url(#blueFill)"/>
    </svg>
    <div class="contact">
      <div class="contact__name">DARA QUILL</div>
      <div class="contact__role">President</div>
      <div class="contact__address">4870 West 63rd Avenue, Suite C207<br>Phoenix AZ 85731</div>
      <ul class="contact__lines">
        <li>
          <svg viewBox="0 0 12 12"><path d="M2.5 1 L4.5 1 L5.3 3.6 L4 4.6 C4.6 6 6 7.4 7.4 8 L8.4 6.7 L11 7.5 L11 9.5 C11 10.3 10.3 11 9.5 11 C5 11 1 7 1 2.5 C1 1.7 1.7 1 2.5 1 Z" fill="var(--brand-green)"/></svg>
          555-014-2730
        </li>
        <li>
          <svg viewBox="0 0 12 12"><rect x="1" y="2.5" width="10" height="7" fill="none" stroke="var(--brand-green)" stroke-width="1.2"/><path d="M1 2.5 L6 6.5 L11 2.5" fill="none" stroke="var(--brand-green)" stroke-width="1.2"/></svg>
          dara@brightharbortrade.example
        </li>
        <li>
          <svg viewBox="0 0 12 12"><circle cx="6" cy="6" r="5" fill="none" stroke="var(--brand-green)" stroke-width="1.2"/><ellipse cx="6" cy="6" rx="2.2" ry="5" fill="none" stroke="var(--brand-green)" stroke-width="1"/><path d="M1 6 H11" stroke="var(--brand-green)" stroke-width="1"/></svg>
          www.brightharbortrade.example
        </li>
      </ul>
    </div>
    <div class="brand">
      <span class="brand__dot"></span>
      <div>
        <div class="brand__name">BrightHarborTrade.example</div>
        <div class="brand__tagline">Activities-Dining-Health-Beauty</div>
      </div>
    </div>
  </section>

</body>
</html>
```